Killer Webpage Design

I currently have a self-hosted webpage through wordpress at www.velmarqstudio.com - the content is complete and I'm happy with this but I need it designed (no coding) to complete my requirements. I'm happy to take designs which are non-Wordpress if there is specific advantage in this.

My full branding logos are attached along with color files. My main aim is consistent branding across all areas (social media, business cards, emails, websites). I have the rest running but am not happy with the available default selections from Wordpress.

I would prefer to use the darker blue version of the logo as I feel this has more standout in online media, however I would appreciate submissions with both variants to help me choose.

With the homepage I will also want to see blog pages and category pages designed but this can come after I have selected a design to go with,

Sites that I like and are related to my business include the following:
http://www.brindlepath.com/au/accounting-software/
http://www.tasklanternpro.com/home.aspx
https://pelicoin.com/register
Updates

Apologies for the confusion - to clarify for designers I am looking for design only, no coding.

FYI - i have now uploaded business cards for an idea of the contemporary style of design completed so far.

Target Market(s)

small to medium business. Not systemised but looking for help and support.

Industry/Entity Type

Business

Requirements
Must have
• I'm looking for a minimalist professional page, with the ability to easily add new sections when required. I will also need a CMS to add blog posts on the go, with the same features that it currently has (comments, social logon etc)

```html
<!DOCTYPE html>
<html lang="en">
<head>
<meta charset="utf-8">
<title>Velmarq Studio – Specialist Business Consultants</title>
<link href="https://fonts.googleapis.com/css2?family=Source+Sans+3:ital,wght@0,300;0,400;0,600;0,700;1,300;1,400&display=swap" rel="stylesheet">
<style>
  :root {
    --navy: #0a2536;
    --navy-text: #0d2e45;
    --teal-light: #18c6d2;
    --teal-dark: #0ea4b1;
    --accent: #2fc6cf;
    --body-text: #4a4f55;
    --muted: #8a8d90;
    --rule: #e2e4e6;
    --footer-bg: #f4f5f5;
    --white: #ffffff;
  }
  * { margin: 0; padding: 0; box-sizing: border-box; }
  html, body { width: 890px; height: 1200px; overflow: hidden; }
  body {
    position: relative;
    background: var(--white);
    font-family: "Source Sans 3", "Myriad Pro", sans-serif;
    color: var(--body-text);
  }
  .abs { position: absolute; }

  /* Header */
  .site-header { left: 0; top: 0; width: 890px; height: 90px; background: var(--navy); }
  .brand { left: 60px; top: 28px; display: flex; align-items: center; gap: 9px; }
  .brand-dot { width: 30px; height: 30px; border-radius: 50%; background: var(--accent); }
  .brand-name { font-size: 25px; font-weight: 600; color: var(--white); letter-spacing: -0.3px; }
  .main-nav { right: 74px; top: 40px; display: flex; font-size: 13.2px; color: var(--white); }
  .main-nav span { padding: 0 9px; border-left: 1px solid rgba(255,255,255,.55); line-height: 12px; }
  .main-nav span:first-child { border-left: none; }
  .main-nav span:last-child { padding-right: 0; }

  /* Hero */
  .hero { left: 0; top: 90px; width: 890px; height: 344px;
    background: linear-gradient(180deg, var(--teal-light) 0%, var(--teal-dark) 100%); }
  .hero-kicker { left: 94px; top: 140px; font-size: 31px; font-weight: 300; color: var(--white); }
  .hero-title { left: 94px; top: 176px; font-size: 34px; font-weight: 700; color: var(--white); line-height: 37px; }
  .hero-sub { left: 95px; top: 257px; font-size: 15px; font-weight: 400; color: var(--navy-text); }
  .hero-text { left: 95px; top: 280px; width: 290px; font-size: 10px; line-height: 15.5px; color: #0f5a66; }
  .btn-more { left: 95px; top: 321px; width: 94px; height: 28px; background: var(--navy);
    border-radius: 3px; color: var(--white); font-size: 10.5px; text-align: center; line-height: 28px;
    box-shadow: 0 2px 3px rgba(0,0,0,.2); }
  .slider-dots { left: 96px; top: 368px; display: flex; gap: 4.5px; }
  .slider-dots i { width: 10px; height: 10px; border-radius: 50%; background: rgba(255,255,255,.4); }
  .slider-dots i:first-child { background: var(--white); }
  .hero-visual { left: 412px; top: 114px; width: 382px; height: 296px; border-radius: 14px;
    background: linear-gradient(160deg, #ffffff 0%, #eceff1 60%, #d8dde0 100%);
    box-shadow: 0 4px 10px rgba(0,0,0,.12); }

  /* Intro */
  .intro-title { left: 0; top: 469px; width: 890px; text-align: center; font-size: 24px;
    font-weight: 400; color: var(--navy-text); }
  .intro-text { left: 84px; top: 504px; width: 714px; text-align: center; font-size: 11.6px; line-height: 19px; }
  .rule { height: 1px; background: var(--rule); }
  .rule-intro { left: 71px; top: 568px; width: 741px; }

  /* Features */
  .feature { top: 598px; width: 222px; }
  .feature h3 { font-size: 18.5px; font-weight: 400; color: var(--navy-text); height: 28px; }
  .feature-media { width: 222px; height: 92px; }
  .feature h4 { margin-top: 9px; font-size: 11.6px; font-weight: 600; color: #222; }
  .feature p { margin-top: 3px; font-size: 10px; line-height: 16.5px; }
  .media-training { background: linear-gradient(135deg, #3c6a60, #d7dbd4 55%, #2a3136); }
  .media-project { background: linear-gradient(135deg, #2c3340, #c9b39c 50%, #1f2733); }
  .media-services { background: linear-gradient(135deg, #3a5560, #a8b8bc 50%, #e9c43a 80%, #4b6068); }

  .rule-soft { left: 30px; top: 845px; width: 830px; height: 2px;
    background: linear-gradient(90deg, transparent, #e6e8ea 20%, #e6e8ea 80%, transparent); }

  /* Testimonial */
  .video { left: 120px; top: 886px; width: 212px; height: 140px; border: 2px solid var(--white);
    background: linear-gradient(135deg, #b0683a, #e3b79a 45%, #6d4a33);
    box-shadow: 0 6px 18px rgba(0,0,0,.18); }
  .play { left: 213px; top: 942px; }
  .quote-mark { left: 375px; top: 894px; font-size: 42px; font-style: italic; color: #c9ccce; font-family: Georgia, serif; }
  .quote { left: 404px; top: 910px; width: 345px; font-size: 14px; font-style: italic;
    font-weight: 300; line-height: 22.6px; color: #6b6f73; }
  .quote .close { color: #b5b8bb; font-size: 12px; }

  /* Footer */
  .site-footer { left: 0; top: 1078px; width: 890px; height: 122px; background: var(--footer-bg);
    border-top: 1px solid #e4e6e7; }
  .footer-nav { left: 103px; top: 1105px; display: flex; font-size: 13.5px; color: var(--muted); }
  .footer-nav span { padding: 0 11px; border-left: 1px solid #bfc2c4; line-height: 13px; }
  .footer-nav span:first-child { padding-left: 0; border-left: none; }
  .rule-footer { left: 71px; top: 1138px; width: 751px; background: #e0e2e3; }
  .copyright { left: 95px; top: 1155px; font-size: 10px; color: var(--muted); }
  .social { left: 725px; top: 1158px; display: flex; gap: 8px; }
  .social i { width: 18px; height: 18px; border-radius: 50%; background: #4c4f52; }
</style>
</head>
<body>
  <header class="site-header abs">
    <div class="brand abs">
      <div class="brand-dot"></div>
      <div class="brand-name">Velmarq Studio</div>
    </div>
    <nav class="main-nav abs">
      <span>Software Training</span><span>Project Management</span><span>Business Process Analysis</span><span>Blog</span><span>About Us</span>
    </nav>
  </header>

  <section class="hero abs"></section>
  <div class="hero-kicker abs">Velmarq Studio</div>
  <h1 class="hero-title abs">Specialist Business<br>Consultants</h1>
  <div class="hero-sub abs">Vacus vitae vestibulum volutpat.</div>
  <p class="hero-text abs">Mauris vel lacus vitae felis vestibulum volutpat. Etiam est nunc, venenatis in, tristique eu, imperdiet ac, nisl.</p>
  <div class="btn-more abs">READ MORE</div>
  <div class="slider-dots abs"><i></i><i></i><i></i><i></i></div>
  <div class="hero-visual abs" role="img" aria-label="Tablet and phone showing a thoughtful woman surrounded by question marks and a music app"></div>

  <h2 class="intro-title abs">Suspendisse quam leo molestie sed luctus</h2>
  <p class="intro-text abs">Mauris vel lacus vitae felis vestibulum volutpat. Etiam est nunc, venenatis in, tristique eu, imperdiet ac, nisl. Cum sociis natoque penatibus et magnis dis parturient montes, nascetur ridiculus mus. In iaculis facilisis massa.</p>
  <div class="rule rule-intro abs"></div>

  <article class="feature abs" style="left:77px">
    <h3>Training &amp; Process</h3>
    <div class="feature-media media-training" role="img" aria-label="Students cheering in a classroom"></div>
    <h4>Nunc tempus felis vitae urna.</h4>
    <p>Vivamus porttitor, g, purus nisi eleifend libero,<br>a tempus libero lectus feugiat felis. Morbi diam<br>mauris, viverra in, gravida eu, mattis in ante.</p>
  </article>
  <article class="feature abs" style="left:333px">
    <h3>Project Management</h3>
    <div class="feature-media media-project" role="img" aria-label="Business team talking together"></div>
    <h4>Nunc tempus felis vitae urna.</h4>
    <p>Vivamus porttitor, g, purus nisi eleifend libero,<br>a tempus libero lectus feugiat felis. Morbi diam<br>mauris, viverra in, gravida eu, mattis in ante.</p>
  </article>
  <article class="feature abs" style="left:589px">
    <h3>Featured Services</h3>
    <div class="feature-media media-services" role="img" aria-label="Row of light bulbs with one glowing yellow"></div>
    <h4>Nunc tempus felis vitae urna.</h4>
    <p>Vivamus porttitor, g, purus nisi eleifend libero,<br>a tempus libero lectus feugiat felis. Morbi diam<br>mauris, viverra in, gravida eu, mattis in ante.</p>
  </article>

  <div class="rule-soft abs"></div>

  <div class="video abs" role="img" aria-label="Video still of a smiling client giving a testimonial"></div>
  <svg class="play abs" width="28" height="28" viewBox="0 0 28 28" aria-hidden="true">
    <circle cx="14" cy="14" r="12.5" fill="#1c1c1c" stroke="#ffffff" stroke-width="2"/>
    <path d="M11 8.5 L19 14 L11 19.5 Z" fill="#ffffff"/>
  </svg>
  <div class="quote-mark abs">&ldquo;</div>
  <blockquote class="quote abs">Duis tincidunt lectus quis dui viverra vestibulum Suspend-isse vulputate aliquam dui Nulla elementum dui ut augue Aliquam vehicula mi at mauris Maecenas placerat nisl at consequat rhoncus, sem nunc <span class="close">&raquo;</span></blockquote>

  <footer class="site-footer abs"></footer>
  <nav class="footer-nav abs">
    <span>About Us</span><span>Blog</span><span>Project Management</span><span>Software Training</span><span>News</span><span>Testimonials</span><span>Pricing</span><span>Security</span>
  </nav>
  <div class="rule rule-footer abs"></div>
  <div class="copyright abs">© 2013 Company Name Inc. All right reserved</div>
  <div class="social abs"><i></i><i></i><i></i></div>
</body>
</html>
```